Dynamic Business Card for Sports Supplements Company

Hi! I'm looking for an awesome business card to match my existing sports supplement company. I have uploaded my current company logo and screenshot of the front page of my website.

I would like to have something dynamic and interesting and utilize the colors in the website - the reds and purples

The business card should be double sided and focus on a unique eye-catching design on the back and include all the relevant company info.

Most importantly, it should say somewhere: "Sign up on our website for a coupon code."

Target Market(s)

Mostly for women gym goers but it shouldn't be too feminine. It should be in keeping with the website design. It should flow and clearly be connected to it

Industry/Entity Type

Business

Contact Information for Business Card

Lorraine K. Vestal
CEO
LVestal@Quorvanexco.com
www.quorvanexco.com
555.417.3820
P.O. Box 47315
Dunmore, Calvera 00000

Sign up on our website for a coupon code

Font styles to use
Serif
Sans Serif
Other font styles liked:
• Novecento font family and "Quorvanex" is in AR Destine font

Requirements
Must have
• One side should be a bold Quorvanex logo design. Even just the symbol itself may be o.k. (see attached file)

```html
<!DOCTYPE html>
<html lang="en">
<head>
<meta charset="utf-8">
<title>Quorvanex Business Card</title>
<link rel="stylesheet" href="https://fonts.googleapis.com/css2?family=Michroma&family=Ubuntu:wght@400&display=swap">
<style>
  :root {
    --backdrop: #a8a8a8;
    --card-light: #f3f3f3;
    --card-dark: #1a1a1a;
    --brand-red: #e31e24;
    --ink: #1d1d1d;
    --paper-text: #ffffff;
  }
  * { margin: 0; padding: 0; box-sizing: border-box; }
  html, body { width: 1200px; height: 900px; overflow: hidden; }
  body {
    background: var(--backdrop);
    position: relative;
    font-family: "Ubuntu", "Helvetica Neue", Arial, sans-serif;
  }
  .card {
    position: absolute;
    top: 200px;
    width: 310px;
    height: 502px;
  }
  .card-front {
    left: 293px;
    background: var(--card-light);
    border-radius: 62px 0 62px 0;
  }
  .card-back {
    left: 633px;
    width: 309px;
    background: var(--card-dark);
    border-radius: 0 62px 0 62px;
  }
  .brand {
    position: absolute;
    left: 0; right: 0;
    display: flex;
    flex-direction: column;
    align-items: center;
  }
  .brand-mark {
    width: 30px; height: 30px;
    background: var(--brand-red);
    margin-bottom: 22px;
  }
  .brand-name {
    font-family: "Michroma", "Arial Black", sans-serif;
    font-size: 23px;
    letter-spacing: 0.5px;
    line-height: 1;
  }
  .card-front .brand { top: 112px; }
  .card-front .brand-name { color: var(--ink); }
  .card-back .brand { top: 210px; }
  .card-back .brand-name { color: var(--paper-text); }

  .holder {
    position: absolute;
    left: 29px;
    top: 294px;
  }
  .holder-name {
    font-family: "Michroma", "Arial Black", sans-serif;
    color: var(--brand-red);
    font-size: 15px;
    letter-spacing: 0.6px;
    line-height: 1;
  }
  .holder-role {
    color: var(--ink);
    font-size: 14px;
    margin-top: 6px;
    letter-spacing: 0.5px;
  }
  .contact-list {
    position: absolute;
    left: 29px;
    top: 347px;
    list-style: none;
    color: var(--ink);
    font-size: 14px;
  }
  .contact-list li {
    display: flex;
    align-items: center;
    height: 22.5px;
  }
  .contact-list svg {
    width: 13px; height: 13px;
    margin-right: 9px;
    fill: var(--brand-red);
  }
  .address {
    position: absolute;
    left: 29px;
    top: 429px;
    font-size: 14px;
    line-height: 18px;
    color: var(--ink);
    font-style: normal;
  }
  .promo {
    position: absolute;
    left: 0; right: 0;
    top: 396px;
    text-align: center;
    font-size: 14px;
    line-height: 18px;
  }
  .promo-lead { color: var(--brand-red); }
  .promo-rest { color: var(--paper-text); }
</style>
</head>
<body>
  <section class="card card-front">
    <div class="brand">
      <span class="brand-mark"></span>
      <span class="brand-name">QUORVANEX</span>
    </div>

    <div class="holder">
      <p class="holder-name">LORRAINE K. VESTAL</p>
      <p class="holder-role">CEO</p>
    </div>

    <ul class="contact-list">
      <li>
        <svg viewBox="0 0 16 16" aria-hidden="true"><path d="M1 6c0-2 3-4 7-4s7 2 7 4v1h-3.5V5.5h-7V7H1V6zm3 2h8l2 6H2l2-6zm4 1.5a2 2 0 1 0 0 4 2 2 0 0 0 0-4z"/></svg>
        555.417.3820
      </li>
      <li>
        <svg viewBox="0 0 16 16" aria-hidden="true"><path d="M1 3h14v10H1V3zm1.5 1.3v.4L8 9l5.5-4.3v-.4H2.5zm0 2.1v5.3h11V6.4L8 10.7 2.5 6.4z"/></svg>
        LVestal@Quorvanexco.com
      </li>
      <li>
        <svg viewBox="0 0 16 16" aria-hidden="true"><path d="M8 1a7 7 0 1 0 0 14A7 7 0 0 0 8 1zm-1 2.3c.8.6.5 1.5-.3 2-.9.5-.6 1.6.4 1.8 1.3.3 2 1.4 1.4 2.6-.5 1-.2 2.2.5 3-3.2.3-5.8-2.6-5.3-5.7.4-2 1.7-3.4 3.3-3.7zm3.6 1c1.5 1 2.2 2.9 1.7 4.7-.6-.7-1.4-.8-1.8-1.6-.3-.8.4-1.6.1-3.1z"/></svg>
        www.quorvanexco.com
      </li>
    </ul>

    <address class="address">
      P.O. Box 47315<br>
      Dunmore, Calvera 00000
    </address>
  </section>

  <section class="card card-back">
    <div class="brand">
      <span class="brand-mark"></span>
      <span class="brand-name">QUORVANEX</span>
    </div>
    <p class="promo">
      <span class="promo-lead">Sign up</span><br>
      <span class="promo-rest">on our website for a coupon code</span>
    </p>
  </section>
</body>
</html>
```